New Business Card Design

We would like to refresh our business cards and make them look better. We are an IT company specialising in Cloud Services, IT Managed Services, software and hardware. I have attached a PSD of our current design. Also attached our logo.
Updates

I have uploaded all new logos in EPS format.

Can you please edit all designs to include a job title for Marcus Hollis, eg. General Manager

Industry/Entity Type

Software

Colors
ffffff

Requirements
Must have
• Please use white background.
Should not have
• Black background

```html
<!DOCTYPE html>
<html lang="en">
<head>
<meta charset="utf-8">
<title>Meridian Technology – Business Card</title>
<link href="https://fonts.googleapis.com/css2?family=Open+Sans:wght@400;600;700&display=swap" rel="stylesheet">
<style>
  :root {
    --brand-red: #c0392b;
    --ink-navy: #1c2630;
    --card-white: #ffffff;
    --logo-grey: #8e949a;
    --stage: #e9e9ec;
    --on-red: #ffffff;
  }
  * { box-sizing: border-box; margin: 0; padding: 0; }
  html, body {
    width: 1200px; height: 987px; overflow: hidden;
    background: var(--stage);
    font-family: "Open Sans", Arial, sans-serif;
  }
  .sheet {
    width: 1200px; height: 987px;
    display: flex; flex-direction: column; align-items: center; justify-content: center;
    gap: 40px;
  }
  .card {
    position: relative;
    width: 720px; height: 440px;
    border-radius: 28px;
    overflow: hidden;
    box-shadow: 0 6px 18px rgba(0,0,0,0.15);
  }
  /* front */
  .card--front { background: var(--card-white); }
  .card__swoosh { position: absolute; inset: 0; }
  .brand {
    position: absolute; left: 60px; top: 50px;
    display: flex; align-items: center; gap: 18px;
  }
  .brand__mark {
    width: 64px; height: 64px; border-radius: 50%;
    background: var(--brand-red);
  }
  .brand__name {
    font-size: 46px; font-weight: 400; letter-spacing: 6px;
    color: var(--ink-navy); line-height: 1;
  }
  .contact {
    position: absolute; left: 40px; bottom: 44px;
    display: flex; align-items: flex-start; gap: 22px;
    color: var(--on-red);
  }
  .contact__person { text-align: right; }
  .contact__name { font-size: 22px; font-weight: 700; }
  .contact__title { font-size: 16px; }
  .contact__line {
    display: flex; align-items: center; gap: 8px;
    font-size: 17px; margin-top: 4px;
  }
  .contact__person .contact__line { justify-content: flex-end; }
  .contact__divider {
    width: 1px; align-self: stretch;
    background: rgba(255,255,255,0.6);
  }
  .icon { width: 16px; height: 16px; flex: none; }
  /* back */
  .card--back {
    background: var(--brand-red);
    color: var(--on-red);
  }
  .back__mark {
    position: absolute; left: 50%; top: 60px; transform: translateX(-50%);
    width: 150px; height: 150px; border-radius: 50%;
    background: var(--card-white);
  }
  .back__tagline {
    position: absolute; left: 0; right: 0; top: 250px;
    text-align: center; font-size: 21px; line-height: 1.45;
  }
  .back__web {
    position: absolute; left: 0; right: 0; top: 335px;
    text-align: center; font-size: 16px; letter-spacing: 3px;
  }
  .back__web strong { font-weight: 700; }
</style>
</head>
<body>
<main class="sheet">

  <section class="card card--front">
    <svg class="card__swoosh" viewBox="0 0 720 440" width="720" height="440" aria-hidden="true">
      <path d="M0 95 C 120 190, 260 330, 720 340 L 720 440 L 0 440 Z" fill="var(--brand-red)"/>
      <path d="M0 62 C 110 150, 200 300, 560 330 C 300 300, 140 180, 0 84 Z" fill="var(--ink-navy)"/>
    </svg>

    <div class="brand">
      <span class="brand__mark"></span>
      <span class="brand__name">meridian technology</span>
    </div>

    <div class="contact">
      <div class="contact__person">
        <p class="contact__name">Marcus Hollis</p>
        <p class="contact__title">General Manager</p>
        <p class="contact__line">
          <svg class="icon" viewBox="0 0 16 16" aria-hidden="true"><rect x="4" y="1" width="8" height="14" rx="1.5" fill="none" stroke="currentColor" stroke-width="1.5"/><circle cx="8" cy="12.5" r="0.9" fill="currentColor"/></svg>
          0400 555 192
        </p>
      </div>
      <span class="contact__divider"></span>
      <div class="contact__details">
        <p class="contact__line">
          <svg class="icon" viewBox="0 0 16 16" aria-hidden="true"><circle cx="8" cy="8" r="7" fill="none" stroke="currentColor" stroke-width="1.3"/><path d="M5 4.5c0 4 2.5 6.5 6.5 6.5l-.6-1.8-1.6.4-2.4-2.4.4-1.6z" fill="currentColor"/></svg>
          07 5550 1234
        </p>
        <p class="contact__line">
          <svg class="icon" viewBox="0 0 16 16" aria-hidden="true"><rect x="1.5" y="3.5" width="13" height="9" fill="none" stroke="currentColor" stroke-width="1.3"/><path d="M1.5 3.5 8 9l6.5-5.5" fill="none" stroke="currentColor" stroke-width="1.3"/></svg>
          mhollis@meridianit.com.au
        </p>
        <p class="contact__line">
          <svg class="icon" viewBox="0 0 16 16" aria-hidden="true"><circle cx="8" cy="8" r="6.5" fill="none" stroke="currentColor" stroke-width="1.3"/><ellipse cx="8" cy="8" rx="3" ry="6.5" fill="none" stroke="currentColor" stroke-width="1.1"/><path d="M1.5 8h13" stroke="currentColor" stroke-width="1.1"/></svg>
          www.meridianit.com.au
        </p>
      </div>
    </div>
  </section>

  <section class="card card--back">
    <span class="back__mark"></span>
    <p class="back__tagline">We are an IT company specializing in Cloud Services<br>IT Managed Services, software and hardware</p>
    <p class="back__web">www.<strong>meridianit</strong>.com.au</p>
  </section>

</main>
</body>
</html>
```